BrivoTerna. Lantern of the Steady Harvest. Business card

Professional business card for BrivoTerna (Lantern of the Steady Harvest)
My rationale: Strategy-> Execution-> Results-> Value that lead to the BrivoTerna name: We put the Lantern of the Steady Harvest.
We deliver value to our customers helping them at defining a good strategy (cyan arrow). 90% of well formulated strategies fail due to poor execution so we also consider strategical execution very important (green arrow). Due to the execution we obtain the results (blue arrow). Finally, the results provide feedback to redefine strategy, and the new strategy has to be executed and new results obtained providing new feedback and on and on. It's like a wheel that finally, must create corporate value: value for shareholders, staholders, employees, providers...-

Target Market(s)

CEOs and steering comitees , invewrnent funds

Industry/Entity Type

Business Consultant

Contact Information for Business Card

Teodoro Vinsquel
CEO & Founder
teodoro.vinsquel@brivoterna-example.com
Mobile: +34 655.803.912
www.brivoterna-example.com

Colors

Designer to choose colors to be used in the design.

Requirements
Nice to have
• Nice to hace the words: Strategy, execution, results
• Nice to vave the claim: Lantern of the Steady Harvest
• The three colors should be shown:
• cyan for STRATEGY
• green for EXECUTION
• blue for RESULTS
Should not have
• Complete black background

```html
<!DOCTYPE html>
<html lang="en">
<head>
<meta charset="utf-8">
<title>BrivoTerna – Business Card</title>
<link href="https://fonts.googleapis.com/css2?family=Montserrat:wght@300;400;600;700&display=swap" rel="stylesheet">
<style>
  :root {
    --backdrop: #3a3b3d;
    --card-dark: #17181a;
    --card-mid: #2a2b2e;
    --ink-white: #ffffff;
    --ink-soft: #d9d9d9;
    --cyan: #19a7e4;
    --green: #8cc63f;
    --blue: #0aa0e6;
  }
  * { box-sizing: border-box; margin: 0; padding: 0; }
  html, body {
    width: 1200px; height: 852px; overflow: hidden;
    background: var(--backdrop);
    font-family: "Montserrat", Arial, sans-serif;
  }
  .canvas { position: relative; width: 1200px; height: 852px; }
  .card {
    position: absolute; width: 620px; height: 354px;
    border-radius: 18px; overflow: hidden;
    background: linear-gradient(135deg, var(--card-mid) 0%, var(--card-dark) 70%);
    box-shadow: 0 18px 40px rgba(0,0,0,.45);
  }
  .card-front { left: 110px; top: 48px; }
  .card-back  { left: 470px; top: 450px; }

  .brand {
    position: absolute; display: flex; align-items: center; gap: 14px;
    color: var(--ink-white); font-weight: 700; letter-spacing: -0.5px;
  }
  .brand-mark { background: var(--green); flex: none; }
  .card-front .brand { left: 64px; top: 150px; font-size: 56px; }
  .card-front .brand-mark { width: 30px; height: 30px; }
  .card-back .brand { left: 48px; top: 72px; font-size: 40px; }
  .card-back .brand-mark { width: 22px; height: 22px; }

  .person { position: absolute; right: 44px; top: 140px; text-align: right; }
  .person-name { color: var(--cyan); font-weight: 600; font-size: 25px; line-height: 1.1; }
  .person-role { color: var(--ink-soft); font-weight: 400; font-size: 14px; margin-top: 4px; }
  .title-tab { position: absolute; right: 0; top: 136px; width: 16px; height: 40px; background: var(--green); }

  .rule { position: absolute; left: 40px; right: 30px; top: 210px; height: 1px; background: var(--green); }

  .contacts { position: absolute; left: 44px; top: 224px; list-style: none; }
  .contacts li {
    display: flex; align-items: center; gap: 10px;
    color: var(--ink-white); font-size: 14px; font-weight: 400; line-height: 24px;
  }
  .contacts svg { width: 13px; height: 13px; flex: none; }

  .band { position: absolute; left: 0; bottom: 0; width: 620px; height: 40px; }
</style>
</head>
<body>
<main class="canvas">

  <section class="card card-front" aria-label="Card front">
    <div class="brand"><span class="brand-mark"></span>BrivoTerna</div>
  </section>

  <section class="card card-back" aria-label="Card back">
    <div class="brand"><span class="brand-mark"></span>BrivoTerna</div>

    <div class="person">
      <p class="person-name">Teodoro Vinsquel</p>
      <p class="person-role">CEO &amp; Founder</p>
    </div>
    <span class="title-tab"></span>

    <span class="rule"></span>

    <ul class="contacts">
      <li>
        <svg viewBox="0 0 16 16" aria-hidden="true"><path fill="var(--cyan)" d="M3.6 1.2l2.3 2.7-1.3 1.6c.9 2.1 2.4 3.7 4.6 4.9l1.6-1.3 2.8 2.2-1.4 2.5C6.6 13.6 2.4 9.3 1.2 3.1z"/></svg>
        +34 655.803.912
      </li>
      <li>
        <svg viewBox="0 0 16 16" aria-hidden="true"><rect x="1.5" y="3.5" width="13" height="9" rx="1" fill="none" stroke="var(--cyan)" stroke-width="1.6"/><path d="M2 4.5l6 4.5 6-4.5" fill="none" stroke="var(--cyan)" stroke-width="1.6"/></svg>
        teodoro.vinsquel@brivoterna-example.com
      </li>
      <li>
        <svg viewBox="0 0 16 16" aria-hidden="true"><circle cx="8" cy="8" r="6.5" fill="none" stroke="var(--cyan)" stroke-width="1.4"/><path d="M1.5 8h13M8 1.5c-3 3.5-3 9.5 0 13M8 1.5c3 3.5 3 9.5 0 13" fill="none" stroke="var(--cyan)" stroke-width="1.2"/></svg>
        www.brivoterna-example.com
      </li>
    </ul>

    <svg class="band" viewBox="0 0 620 40" preserveAspectRatio="none" aria-hidden="true">
      <polygon points="0,30 370,30 366,40 0,40" fill="var(--blue)"/>
      <polygon points="378,12 620,12 620,40 366,40" fill="var(--green)"/>
    </svg>
  </section>

</main>
</body>
</html>
```